business card - Helicopter Flight Services, Flight School, etc.

We need a business card design for a new helicopter service.

We offer Helicopter Flight Services, Aerial Filming & Photography, Flight School, and Helicopter Tours. In that order.

Summit BladeAir, Inc.
Dennis Tollerby
SummitBladeair@Kestmail.com
626-418-7352

Based at the Brenwick Airport in Van Nuys, CA. The final design should communicate integrity and safety. Pictures or logos at your discretion.

Card back side - surprise me.

```html
<!DOCTYPE html>
<html lang="en">
<head>
<meta charset="utf-8">
<title>Summit BladeAir, Inc. — Business Card</title>
<link rel="stylesheet" href="https://fonts.googleapis.com/css2?family=Michroma&family=Open+Sans:wght@400;600&display=swap">
<style>
  :root {
    --sky-blue: #0a8ff5;
    --slate-grey: #929497;
    --paper: #ffffff;
    --backdrop: #eef0f2;
    --ink-white: #ffffff;
  }
  * { margin: 0; padding: 0; box-sizing: border-box; }
  html, body { width: 1200px; height: 900px; overflow: hidden; }
  body {
    position: relative;
    background: var(--backdrop);
    font-family: "Open Sans", Arial, sans-serif;
  }
  .card {
    position: absolute;
    width: 556px;
    height: 345px;
    box-shadow: 0 6px 20px rgba(0,0,0,0.12);
    overflow: hidden;
  }
  /* Front */
  .card-front {
    left: 237px; top: 60px;
    background: var(--sky-blue);
    color: var(--ink-white);
  }
  .front-art {
    position: absolute;
    right: 0; top: 0;
    width: 230px; height: 345px;
    background: linear-gradient(180deg, #a2a4a7 0%, var(--slate-grey) 100%);
    clip-path: polygon(30% 0, 100% 0, 100% 100%, 0 100%, 0 35%);
  }
  .company-name {
    position: absolute;
    left: 43px; top: 84px;
    font-family: "Michroma", Arial, sans-serif;
    font-size: 21px;
    line-height: 31px;
    letter-spacing: 1px;
    text-transform: uppercase;
  }
  .person-name {
    position: absolute;
    left: 43px; top: 188px;
    font-size: 18px;
    font-weight: 600;
  }
  .contact-list {
    position: absolute;
    left: 46px; top: 230px;
    list-style: none;
    font-size: 14.5px;
    line-height: 21px;
  }
  .contact-list li { display: flex; align-items: center; gap: 9px; }
  .contact-list svg { width: 11px; height: 11px; fill: var(--ink-white); }
  /* Back */
  .card-back {
    left: 457px; top: 517px;
    width: 560px;
    background: var(--paper);
  }
  .brand-mark {
    position: absolute;
    left: 0; right: 0; top: 100px;
    display: flex; align-items: center; justify-content: center; gap: 14px;
  }
  .brand-dot {
    width: 40px; height: 40px;
    border-radius: 50%;
    background: var(--sky-blue);
  }
  .brand-name {
    font-family: "Michroma", Arial, sans-serif;
    font-size: 19px;
    line-height: 27px;
    color: var(--sky-blue);
    text-transform: uppercase;
  }
  .service-list {
    position: absolute;
    left: 0; right: 0; top: 245px;
    text-align: center;
    color: var(--sky-blue);
    font-size: 14.5px;
    font-weight: 600;
    line-height: 25px;
  }
</style>
</head>
<body>
  <section class="card card-front">
    <div class="front-art" role="img" aria-label="Large grey helicopter emblem decoration"></div>
    <h1 class="company-name">Summit<br>BladeAir<br>Inc.</h1>
    <p class="person-name">Dennis Tollerby</p>
    <ul class="contact-list">
      <li>
        <svg viewBox="0 0 24 24" aria-hidden="true"><path d="M6.6 10.8a15 15 0 0 0 6.6 6.6l2.2-2.2c.3-.3.7-.4 1-.2 1.1.4 2.3.6 3.6.6.6 0 1 .4 1 1V20c0 .6-.4 1-1 1A17 17 0 0 1 3 4c0-.6.4-1 1-1h3.5c.6 0 1 .4 1 1 0 1.3.2 2.5.6 3.6.1.3 0 .7-.2 1z"/></svg>
        626-418-7352
      </li>
      <li>
        <svg viewBox="0 0 24 24" aria-hidden="true"><path d="M2 5h20v14H2z M2 5l10 7 10-7" stroke="#0a8ff5" stroke-width="1.5"/></svg>
        SummitBladeair@Kestmail.com
      </li>
    </ul>
  </section>

  <section class="card card-back">
    <div class="brand-mark">
      <span class="brand-dot" aria-hidden="true"></span>
      <span class="brand-name">Summit<br>BladeAir<br>Inc.</span>
    </div>
    <p class="service-list">
      Helicopter Flight Services | Aerial Filming &amp; Photography,<br>
      Flight School | Helicopter Tours
    </p>
  </section>
</body>
</html>
```